Website for IT consulting Company

I need a website upgrade, the existing site content is ok, I would also like to add a testimonial page, the site should be something that is easy for us to update content. You use the content from www.kelvanbrook.com as an example. I will also post update logo and artwork. I also need a contact form with some type of validation or captcha.

I added Coded to the Project

Please omit Address maps

Target Market(s)

small business, service oriented companies. We provide IT Consulting, support and mangement

Industry/Entity Type

Information Technology

Coding

Number of Pages Required

1 page

Font styles to use
Serif
Sans Serif

Requirements
Must have
• Contain logo attached, and content from existing web site www.kelvanbrook.com.
• Also need to update content easily, and be movable to different platforms.
• There is a catch phrase
• "Let us worry about your technology…” “ so you don’t have to!”
• Should be included.
Nice to have
• Testimonial page, Project page where we can post new and past projects and pictures
Should not have
• none

```html
<!DOCTYPE html>
<html lang="en">
<head>
<meta charset="utf-8">
<title>Kelvanbrook Development Group – IT Consulting</title>
<link href="https://fonts.googleapis.com/css2?family=Exo+2:ital,wght@0,600;0,700;0,800;1,600;1,700;1,800&family=Arimo:wght@400;700&family=Tinos&display=swap" rel="stylesheet">
<style>
:root{
  --blue:#1e8fd6;
  --blue-dark:#0f6fb3;
  --blue-light:#2aa6e8;
  --ink:#1d1d1d;
  --text:#333;
  --grey-bg:#e9e9e9;
  --grey-mid:#8d8d8d;
  --grey-dark:#6f6f6f;
  --topbar:#2b2b2b;
  --footer:#2a2d33;
  --white:#fff;
}
*{box-sizing:border-box;margin:0;padding:0}
html,body{width:1200px;height:2927px;overflow:hidden}
body{position:relative;background:var(--white);font-family:"Arimo",Arial,sans-serif;color:var(--text)}
.abs{position:absolute}
.head-font{font-family:"Exo 2",sans-serif}

/* top bar */
.topbar{left:0;top:0;width:1200px;height:39px;background:var(--topbar)}
.topbar .social-sq{position:absolute;top:7px;width:24px;height:24px;background:#8a8a8a;border-radius:2px}

/* header */
.header{left:0;top:39px;width:1200px;height:86px;background:var(--white)}
.brand{position:absolute;left:80px;top:14px;display:flex;align-items:center;gap:12px}
.brand .mark{width:48px;height:48px;background:var(--blue);border-radius:4px}
.brand .name{font-family:"Exo 2",sans-serif;font-weight:800;font-size:40px;color:#6e6e6e;letter-spacing:1px;line-height:1}
.tagline{position:absolute;left:142px;top:62px;font-size:9px;color:var(--blue);font-style:italic}
.header-phone{position:absolute;right:58px;top:30px;display:flex;align-items:center;gap:14px;font-family:"Exo 2",sans-serif;font-style:italic;font-weight:600;font-size:21px;color:#555}
.phone-box{width:28px;height:28px;background:var(--blue);border-radius:3px;display:flex;align-items:center;justify-content:center}

/* nav */
.nav{left:0;top:125px;width:1200px;height:56px;background:linear-gradient(#2ea3e6,#1a86cc)}
.nav ul{list-style:none;display:flex;position:absolute;left:98px;top:0;height:56px;align-items:center}
.nav li{font-family:"Exo 2",sans-serif;font-style:italic;font-weight:700;font-size:18px;color:var(--white);text-transform:uppercase;margin-right:63px;letter-spacing:.5px}
.nav li.active{color:#17344f}

/* hero */
.hero{left:0;top:181px;width:1200px;height:533px;background:radial-gradient(ellipse at 30% 30%,#0f3f78 0%,#0a2348 45%,#061529 100%);overflow:hidden}
.hero-art{position:absolute;left:0;top:0;width:520px;height:533px;background:radial-gradient(circle at 210px 170px,#6fd3ff 0%,#1a7fd0 22%,rgba(10,50,110,.4) 48%,rgba(6,21,41,0) 70%)}
.hero-line1{position:absolute;right:62px;top:170px;font-family:"Exo 2",sans-serif;font-style:italic;font-weight:700;font-size:33px;color:var(--white)}
.hero-line2{position:absolute;right:62px;top:214px;font-family:"Exo 2",sans-serif;font-style:italic;font-weight:800;font-size:35px;color:var(--blue-light)}
.call-btn{position:absolute;left:835px;top:279px;width:208px;height:54px;background:linear-gradient(#2ea3e6,#1676bb);border:2px solid #bfe4fa;border-radius:8px;display:flex;align-items:center;gap:8px;padding-left:10px}
.call-btn .txt{font-family:"Exo 2",sans-serif;font-style:italic;font-weight:700;font-size:17px;color:var(--white);line-height:1.05}
.call-sq{position:absolute;left:1040px;top:276px;width:54px;height:54px;background:#8a8a8a;border-radius:4px}
.slide-arrow{position:absolute;top:231px;width:40px;height:34px;background:#4a4a4a;display:flex;align-items:center;justify-content:center}

/* welcome */
.welcome h1{position:absolute;left:84px;top:766px;font-family:"Exo 2",sans-serif;font-style:italic;font-weight:800;font-size:25px;color:var(--ink);text-transform:uppercase}
.welcome h1 span{color:var(--blue)}
.welcome .rule{position:absolute;left:84px;top:803px;width:600px;height:2px;background:#d5d5d5}
.welcome .copy{position:absolute;left:84px;top:828px;width:634px;font-size:13.4px;line-height:25px;color:var(--text)}
.welcome .copy p{margin-bottom:6px}
.inquiry{position:absolute;left:765px;top:757px;width:353px;height:330px;background:#ececec;border:1px solid #dcdcdc}
.inquiry .tab{position:absolute;left:46px;top:-6px;width:264px;height:44px;background:linear-gradient(#9b9b9b,#6d6d6d);font-family:"Exo 2",sans-serif;font-style:italic;font-weight:700;font-size:21px;color:var(--white);display:flex;align-items:center;justify-content:center}
.inquiry .field{position:absolute;left:20px;width:314px;height:36px;background:var(--white);border:1px solid #d0d0d0;font-size:11px;color:#777;padding:12px 10px 0}
.inquiry .submit{position:absolute;left:27px;top:273px;width:122px;height:38px;background:linear-gradient(#2ea3e6,#1676bb);font-family:"Exo 2",sans-serif;font-style:italic;font-weight:700;font-size:19px;color:var(--white);display:flex;align-items:center;justify-content:center}

/* services */
.services{left:0;top:1141px;width:1200px;height:572px;background:var(--grey-bg);overflow:hidden}
.section-title{position:absolute;width:100%;text-align:center;font-family:"Exo 2",sans-serif;font-style:italic;font-weight:800;font-size:29px;color:var(--ink);text-transform:uppercase}
.section-title span{color:var(--blue)}
.title-rule{position:absolute;left:570px;width:60px;height:3px;background:var(--blue)}
.svc-label{position:absolute;font-family:"Exo 2",sans-serif;font-style:italic;font-weight:800;font-size:16px;color:#2a2a2a;text-transform:uppercase;line-height:17px}
.svc-label.right{text-align:right}
.services svg{position:absolute;left:0;top:0}
.center-name{position:absolute;left:0;width:1200px;top:452px;display:flex;justify-content:center;align-items:center;gap:12px}
.center-name .sq{width:40px;height:40px;background:var(--blue);border-radius:4px}
.center-name .nm{font-family:"Exo 2",sans-serif;font-weight:800;font-size:46px;color:#777;letter-spacing:1px}

/* info panels */
.panel{top:1713px;height:388px}
.panel-left{left:0;width:605px;background:linear-gradient(160deg,#2ba6e9,#136eb4)}
.panel-right{left:605px;width:595px;background:linear-gradient(160deg,#d9d9d9,#8f8f8f)}
.notch{left:575px;top:1713px;width:60px;height:32px}
.panel h2{position:absolute;font-family:"Exo 2",sans-serif;font-style:italic;font-weight:800;font-size:23px;text-transform:uppercase}
.panel .rule{position:absolute;width:52px;height:2px}
.panel .photo{position:absolute;top:125px;width:211px;height:190px}
.panel .txt{position:absolute;top:125px;width:265px;font-size:13.4px;line-height:23px}
.read-more{position:absolute;top:280px;width:152px;height:38px;font-family:"Tinos",serif;font-size:17px;display:flex;align-items:center;justify-content:center;gap:10px;color:var(--white)}

/* testimonials */
.testimonial .quote{position:absolute;left:210px;top:2230px;width:780px;text-align:center;font-style:italic;font-size:14.4px;line-height:30px;color:#333}
.testimonial .qm{font-family:"Tinos",serif;font-size:40px;color:#aaa;position:absolute}
.testimonial .who{position:absolute;left:0;width:1200px;text-align:center;font-weight:700;font-size:15.5px;color:#222}
.chev{position:absolute;top:2296px}

/* call band */
.cta{left:0;top:2458px;width:1200px;height:98px;background:linear-gradient(#2ea3e6,#1a86cc)}
.cta .l1{position:absolute;left:84px;top:10px;font-family:"Exo 2",sans-serif;font-style:italic;font-weight:700;font-size:33px;color:var(--white)}
.cta .l2{position:absolute;left:84px;top:52px;font-family:"Exo 2",sans-serif;font-style:italic;font-weight:700;font-size:27px;color:var(--white)}
.cta .btn{position:absolute;left:852px;top:22px;width:210px;height:50px;background:linear-gradient(#a3a3a3,#6f6f6f);border:2px solid #ddd;border-radius:8px;display:flex;align-items:center;gap:8px;padding-left:10px;font-family:"Exo 2",sans-serif;font-style:italic;font-weight:700;font-size:17px;color:var(--white);line-height:1.05}
.cta .sq{position:absolute;left:1056px;top:16px;width:52px;height:52px;background:var(--blue);border-radius:4px}

/* footer */
.footer{left:0;top:2556px;width:1200px;height:326px;background:linear-gradient(#3a3e45,#1f2227)}
.footer h3{position:absolute;top:56px;font-family:"Exo 2",sans-serif;font-style:italic;font-weight:800;font-size:18px;color:var(--white)}
.footer h3 span{color:var(--blue-light)}
.footer .rule{position:absolute;top:82px;height:1px;background:#666}
.footer ul{list-style:none;position:absolute}
.footer li{font-size:13.4px;color:#ddd;line-height:24.5px}
.quick li::before{content:"";display:inline-block;width:4px;height:4px;background:var(--blue-light);margin-right:10px;vertical-align:middle}
.contact-line{position:absolute;font-size:13.4px;color:#ddd;display:flex;align-items:center;gap:10px}
.soc-row{position:absolute;left:654px;display:flex;align-items:center;gap:14px;font-size:13.4px;color:#ddd}
.soc-row .box{width:28px;height:28px;background:#8f8f8f;border-radius:2px}
.footer-brand{position:absolute;left:900px;top:150px;display:flex;align-items:center;gap:12px}
.footer-brand .sq{width:60px;height:60px;background:var(--blue);border-radius:6px}
.footer-brand .nm{font-family:"Exo 2",sans-serif;font-weight:800;font-size:30px;color:var(--white)}
.copyright{left:0;top:2882px;width:1200px;height:45px;background:var(--blue);display:flex;align-items:center;justify-content:center;font-size:14.4px;color:var(--white)}
</style>
</head>
<body>

<div class="abs topbar">
  <span class="social-sq" style="left:978px"></span>
  <span class="social-sq" style="left:1008px"></span>
  <span class="social-sq" style="left:1038px"></span>
  <span class="social-sq" style="left:1068px"></span>
</div>

<header class="abs header">
  <div class="brand"><span class="mark"></span><span class="name">KELVANBROOK</span></div>
  <div class="tagline">Let us worry about your technology... So you don't have to!</div>
  <div class="header-phone">
    <span class="phone-box"><svg width="16" height="16" viewBox="0 0 24 24"><path d="M6.6 10.8a15 15 0 0 0 6.6 6.6l2.2-2.2c.3-.3.7-.4 1-.2 1.1.4 2.3.6 3.6.6.6 0 1 .4 1 1V20c0 .6-.4 1-1 1A17 17 0 0 1 3 4c0-.6.4-1 1-1h3.5c.6 0 1 .4 1 1 0 1.3.2 2.5.6 3.6.1.3 0 .7-.2 1z" fill="#fff"/></svg></span>
    (555) 014-2290
  </div>
</header>

<nav class="abs nav">
  <ul>
    <li class="active">Home</li><li>About Us</li><li>Services</li><li>Support</li><li>Clients</li><li>Careers</li><li>Contact Us</li>
  </ul>
</nav>

<section class="abs hero">
  <div class="hero-art" role="img" aria-label="Glowing digital globe held above an open hand"></div>
  <div class="hero-line1">Let Us Worry About Your Technology...</div>
  <div class="hero-line2">So You Don't Have To!</div>
  <div class="call-btn">
    <svg width="28" height="28" viewBox="0 0 24 24"><path d="M6.6 10.8a15 15 0 0 0 6.6 6.6l2.2-2.2c.3-.3.7-.4 1-.2 1.1.4 2.3.6 3.6.6.6 0 1 .4 1 1V20c0 .6-.4 1-1 1A17 17 0 0 1 3 4c0-.6.4-1 1-1h3.5c.6 0 1 .4 1 1 0 1.3.2 2.5.6 3.6.1.3 0 .7-.2 1z" fill="#fff"/></svg>
    <span class="txt">Call Us Today<br>(555) 014-2290</span>
  </div>
  <span class="call-sq"></span>
  <div class="slide-arrow" style="left:4px"><svg width="12" height="14"><path d="M10 1 2 7l8 6z" fill="#ddd"/></svg></div>
  <div class="slide-arrow" style="left:1156px"><svg width="12" height="14"><path d="M2 1l8 6-8 6z" fill="#ddd"/></svg></div>
</section>

<section class="welcome">
  <h1>Welcome to Kelvanbrook <span>Development Group, Inc</span></h1>
  <div class="rule"></div>
  <div class="copy">
    <p>Kelvanbrook Development Group, Inc. was established in 1991. Our mission is helping businesses and individuals realize a Return on Investment by implementing today's advanced technologies. As a small business we understand the importance of technology and personalized attention. Every member of our support team has worked with both large and small companies supporting a multitude of applications, networks and environments.</p>
    <p>We interface daily with Clients and their customers to establish your support needs. A prerequisite for working with Kelvanbrook is having both the technological knowledge and the customer skills to communicate and work with customers to resolve technology issues. Whether it is a simple computer network, phone systems, or an advanced integrated infrastructure, we will study your requirements, suggest methodologies, and implement the design.</p>
  </div>
  <form class="inquiry">
    <div class="tab">Quick Inquiry</div>
    <div class="field" style="top:55px">First Name</div>
    <div class="field" style="top:97px">Email</div>
    <div class="field" style="top:139px">Phone</div>
    <div class="field" style="top:181px;height:80px">Message</div>
    <div class="submit">Submit</div>
  </form>
</section>

<section class="abs services">
  <h2 class="section-title" style="top:42px">Our <span>Services</span></h2>
  <div class="title-rule" style="top:86px"></div>

  <svg width="1200" height="572" viewBox="0 0 1200 572">
    <path d="M376 572 A240 240 0 0 1 854 572" fill="none" stroke="#9a9a9a" stroke-width="9"/>
    <g stroke="#a5a5a5" stroke-width="2" stroke-dasharray="3 4">
      <line x1="427" y1="403" x2="386" y2="371"/>
      <line x1="462" y1="368" x2="392" y2="283"/>
      <line x1="535" y1="327" x2="497" y2="219"/>
      <line x1="615" y1="313" x2="615" y2="201"/>
      <line x1="688" y1="325" x2="722" y2="219"/>
      <line x1="768" y1="368" x2="839" y2="283"/>
      <line x1="819" y1="427" x2="909" y2="371"/>
      <line x1="849" y1="501" x2="956" y2="478"/>
    </g>
    <line x1="380" y1="504" x2="273" y2="482" stroke="#d33" stroke-width="2" stroke-dasharray="3 4"/>
    <g fill="#fff" stroke="#9a9a9a" stroke-width="3">
      <circle cx="427" cy="403" r="7"/><circle cx="462" cy="368" r="7"/><circle cx="535" cy="327" r="7"/>
      <circle cx="615" cy="313" r="7"/><circle cx="688" cy="325" r="7"/><circle cx="768" cy="368" r="7"/>
      <circle cx="819" cy="427" r="7"/><circle cx="849" cy="501" r="7"/>
    </g>
    <circle cx="380" cy="504" r="8" fill="#fff" stroke="#d33" stroke-width="3"/>

    <g fill="#8a8a8a" stroke="#fff" stroke-width="3">
      <circle cx="386" cy="371" r="45"/><circle cx="392" cy="283" r="45"/><circle cx="497" cy="219" r="45"/>
      <circle cx="615" cy="201" r="45"/><circle cx="722" cy="219" r="45"/><circle cx="839" cy="283" r="45"/>
      <circle cx="909" cy="371" r="45"/><circle cx="956" cy="478" r="45"/>
    </g>
    <circle cx="273" cy="482" r="45" fill="var(--blue)" stroke="#fff" stroke-width="3"/>

    <g fill="none" stroke="#fff" stroke-width="3" stroke-linecap="round">
      <!-- desktop support: laptop -->
      <rect x="253" y="466" width="40" height="26" rx="2"/><line x1="246" y1="498" x2="300" y2="498"/>
      <!-- network administration: person + screen -->
      <circle cx="376" cy="360" r="7"/><path d="M363 386c0-9 6-14 13-14s13 5 13 14"/><rect x="390" y="368" width="16" height="12"/>
      <!-- telecommunications: antenna -->
      <line x1="392" y1="278" x2="392" y2="305"/><path d="M382 305l10-27 10 27"/><path d="M380 268a16 16 0 0 0 0 20M404 268a16 16 0 0 1 0 20"/>
      <!-- audio/video: pause -->
      <circle cx="497" cy="219" r="20"/><line x1="491" y1="210" x2="491" y2="228"/><line x1="503" y1="210" x2="503" y2="228"/>
      <!-- disaster recovery: server -->
      <rect x="597" y="182" width="36" height="10" rx="2"/><rect x="597" y="196" width="36" height="10" rx="2"/><circle cx="626" cy="218" r="7"/>
      <!-- web design: devices -->
      <rect x="700" y="204" width="30" height="22" rx="2"/><rect x="734" y="210" width="12" height="20" rx="2"/>
      <!-- network cabling: plug -->
      <rect x="828" y="272" width="18" height="14" rx="2"/><line x1="833" y1="272" x2="833" y2="265"/><line x1="841" y1="272" x2="841" y2="265"/><path d="M837 286v10c0 6 8 6 8 12"/>
      <!-- wireless: router -->
      <rect x="889" y="374" width="40" height="12" rx="3"/><path d="M899 364a14 14 0 0 1 20 0M894 358a22 22 0 0 1 30 0"/>
      <!-- antivirus: shield -->
      <path d="M956 458l17 6v12c0 12-8 19-17 23-9-4-17-11-17-23v-12z"/>
    </g>
  </svg>

  <div class="svc-label" style="left:520px;width:200px;text-align:center;top:126px">Disaster Recovery</div>
  <div class="svc-label right" style="left:149px;width:300px;top:184px">Audio/Video Multimedia</div>
  <div class="svc-label right" style="left:30px;width:300px;top:260px">Telecommunications</div>
  <div class="svc-label right" style="left:50px;width:200px;top:345px">Network<br>Administration</div>
  <div class="svc-label right" style="left:60px;width:145px;top:473px">Desktop<br>Support</div>
  <div class="svc-label" style="left:784px;top:176px">Web Design</div>
  <div class="svc-label" style="left:899px;top:260px">Network Cabling</div>
  <div class="svc-label" style="left:981px;top:353px">Wireless<br>Networks</div>
  <div class="svc-label" style="left:1014px;top:464px">Antivirus<br>Solutions</div>

  <div class="center-name"><span class="sq"></span><span class="nm">KELVANBROOK</span></div>
</section>

<section class="abs panel panel-left">
  <h2 style="left:130px;top:66px;color:#fff">IT Support Solutions</h2>
  <svg class="abs" style="left:86px;top:60px" width="32" height="36" viewBox="0 0 32 36"><circle cx="16" cy="10" r="8" fill="#fff"/><path d="M2 36c0-10 6-15 14-15s14 5 14 15z" fill="#fff"/></svg>
  <div class="rule" style="left:86px;top:108px;background:#fff"></div>
  <div class="photo" style="left:86px;background:linear-gradient(135deg,#3c5b7d,#9fb2c6)" role="img" aria-label="Technicians working beside server racks in a data center"></div>
  <p class="txt" style="left:310px;color:#fff">Lorem ipsum dolor sit amet, consecterr etuer adipiscing elit, sed diam nonumre my nibh euismod tinciduntol ut laoreet et re olore magna aliquam erat volutpt. Ut wisi minim consequat.</p>
  <div class="read-more" style="left:310px;background:linear-gradient(#a9a9a9,#7d7d7d)">Read More <span>&rarr;</span></div>
</section>

<section class="abs panel panel-right">
  <h2 style="left:60px;top:66px;color:#1d1d1d">Why Outsource Technologies</h2>
  <svg class="abs" style="left:30px;top:60px" width="30" height="34" viewBox="0 0 30 34"><circle cx="15" cy="9" r="6" fill="#1d1d1d"/><circle cx="5" cy="13" r="4" fill="#1d1d1d"/><circle cx="25" cy="13" r="4" fill="#1d1d1d"/><path d="M4 34c0-10 5-15 11-15s11 5 11 15z" fill="#1d1d1d"/></svg>
  <div class="rule" style="left:30px;top:108px;background:#1d1d1d"></div>
  <div class="photo" style="left:31px;background:radial-gradient(circle at 50% 40%,#4fa8e6,#0d2a52 70%)" role="img" aria-label="Digital globe and floating app screens above a tablet"></div>
  <p class="txt" style="left:253px;color:#fff">Lorem ipsum dolor sit amet, consecterr etuer adipiscing elit, sed diam nonumre my nibh euismod tincidunt ut laoreet et re olore magna aliquam erat volutpt. Ut wisi minim consequat.</p>
  <div class="read-more" style="left:253px;background:linear-gradient(#2ea3e6,#1676bb)">Read More <span>&rarr;</span></div>
</section>
<svg class="abs notch" viewBox="0 0 60 32"><path d="M0 0h60L30 32z" fill="var(--grey-bg)"/></svg>

<section class="testimonial">
  <h2 class="section-title" style="top:2153px">Clients <span>Testimonials</span></h2>
  <div class="title-rule" style="top:2195px"></div>
  <span class="qm" style="left:212px;top:2222px">&ldquo;</span>
  <p class="quote">Lorem ipsum dolor sit amet, consectetuer adipiscing elit, sed diam nonummy nibh euismod tinciduntol ut laoreet dolore magna aliquam erat volutpat. Ut wisi enim ad minim veniam, quis nostrud exercitomi morskle tation ullamcorper suscipit lobortis nisl ut aliquip ex ea commodo consequat.</p>
  <span class="qm" style="left:886px;top:2290px">&rdquo;</span>
  <div class="who" style="top:2360px">Marla T.</div>
  <div class="who" style="top:2386px;font-size:14.4px">Lakeview, CA</div>
  <svg class="chev" style="left:112px" width="34" height="60"><path d="M30 2 4 30l26 28" fill="none" stroke="#bbb" stroke-width="2"/></svg>
  <svg class="chev" style="left:1052px" width="34" height="60"><path d="M4 2l26 28L4 58" fill="none" stroke="#bbb" stroke-width="2"/></svg>
</section>

<section class="abs cta">
  <div class="l1">IT Solutions That Work For Your Business</div>
  <div class="l2">A Full Service Technology Company</div>
  <div class="btn">
    <svg width="26" height="26" viewBox="0 0 24 24"><path d="M6.6 10.8a15 15 0 0 0 6.6 6.6l2.2-2.2c.3-.3.7-.4 1-.2 1.1.4 2.3.6 3.6.6.6 0 1 .4 1 1V20c0 .6-.4 1-1 1A17 17 0 0 1 3 4c0-.6.4-1 1-1h3.5c.6 0 1 .4 1 1 0 1.3.2 2.5.6 3.6.1.3 0 .7-.2 1z" fill="#fff"/></svg>
    <span>Call Us Today<br>(555) 014-2290</span>
  </div>
  <span class="sq"></span>
</section>

<footer class="abs footer" role="img" aria-label="Dim city skyline at dusk behind the footer">
  <h3 style="left:86px">Quick <span>Links</span></h3>
  <div class="rule" style="left:86px;width:100px"></div>
  <ul class="quick" style="left:86px;top:96px">
    <li>Home</li><li>About Us</li><li>Services</li><li>Support</li><li>Clients</li><li>Careers</li><li>Contact Us</li>
  </ul>

  <h3 style="left:318px">Contact <span>Details</span></h3>
  <div class="rule" style="left:318px;width:120px"></div>
  <div class="contact-line" style="left:318px;top:100px">Kelvanbrook Development Group, Inc.</div>
  <div class="contact-line" style="left:318px;top:134px;display:block;line-height:22px">418 Marlow Ave.<br>Fairview, Texas 75069</div>
  <div class="contact-line" style="left:318px;top:190px"><svg width="14" height="14" viewBox="0 0 24 24"><path d="M6.6 10.8a15 15 0 0 0 6.6 6.6l2.2-2.2c.3-.3.7-.4 1-.2 1.1.4 2.3.6 3.6.6.6 0 1 .4 1 1V20c0 .6-.4 1-1 1A17 17 0 0 1 3 4c0-.6.4-1 1-1h3.5c.6 0 1 .4 1 1 0 1.3.2 2.5.6 3.6.1.3 0 .7-.2 1z" fill="#2aa6e8"/></svg>(555) 014-2290</div>
  <div class="contact-line" style="left:318px;top:222px"><svg width="14" height="14" viewBox="0 0 24 24"><rect x="3" y="8" width="18" height="10" rx="2" fill="#2aa6e8"/><rect x="6" y="3" width="12" height="6" fill="#2aa6e8"/></svg>(555) 014-2290</div>
  <div class="contact-line" style="left:318px;top:254px"><svg width="14" height="12" viewBox="0 0 24 18"><rect x="1" y="1" width="22" height="16" rx="2" fill="#2aa6e8"/><path d="M2 2l10 8 10-8" fill="none" stroke="#fff" stroke-width="2"/></svg>info@kelvanbrook.com</div>

  <h3 style="left:654px">Get <span>Social</span></h3>
  <div class="rule" style="left:654px;width:100px"></div>
  <div class="soc-row" style="top:98px"><span class="box"></span>Pageboard</div>
  <div class="soc-row" style="top:142px"><span class="box"></span>Chirpline</div>
  <div class="soc-row" style="top:186px"><span class="box"></span>Circleplus</div>
  <div class="soc-row" style="top:230px"><span class="box"></span>Workgrid</div>

  <div class="footer-brand"><span class="sq"></span><span class="nm">KELVANBROOK</span></div>
</footer>

<div class="abs copyright">Copyright &copy; 2017 Kelvanbrook Development Group, Inc. All Rights Reserved.</div>

</body>
</html>
```